Australian Trucking Company Requires Professional Looking Stationary

We require a professional looking stationary design that incorporates our newly designed logo.

Our business, called "Brell Haulage Contracting", provides contracting work, transport and logistics to business in Western Australia particularly with links to the mining sector.

We are a small business looking to expand and our new logo and our new stationary will help develop our brand image in our market place.

Target Market(s)

Businesses and Corporation with links to the Mining Sector

Industry/Entity Type

Small Business

Requirements
Must have
• The letterhead must have the following details:
The new logo

Text saying: "Brell Holdings Pty Ltd (ACN 582 316 907) ATF The Brell Discretionary Trust T/AS"
"ABN 71 834 209 553"
Address "P.O Box 817 Wattlegrove WA, 6958"
Phone: 08 9352 7140
Email: brellhaul@mailbox-example.com.au

The text on the letterhead should be editable as the details are likely to change in the near future. Provision should be made for a website address all though one isn't available at the moment.

The styling, layout and font text is entirely up to the designer.

```html
<!DOCTYPE html>
<html lang="en">
<head>
<meta charset="utf-8">
<title>Brell Haulage Contracting – Stationery Set</title>
<link href="https://fonts.googleapis.com/css2?family=Roboto:wght@400;700&family=Roboto+Condensed:wght@700&display=swap" rel="stylesheet">
<style>
  :root{
    --red:#c3121c;
    --red-deep:#7c0a11;
    --red-light:#e0303a;
    --grey:#6d6d6d;
    --grey-light:#bdbdbd;
    --ink:#333;
    --paper:#ffffff;
    --backdrop:#e8e5e1;
  }
  *{box-sizing:border-box;margin:0;padding:0}
  html,body{width:1200px;height:282px;overflow:hidden;background:var(--backdrop)}
  body{font-family:"Roboto",Arial,sans-serif;color:var(--ink)}
  .canvas{position:relative;width:1200px;height:282px;overflow:hidden}

  .sheet{position:absolute;background:var(--paper);box-shadow:0 1px 3px rgba(0,0,0,.25);overflow:hidden}
  .letter{top:35px;width:152px;height:215px}
  .option-label{position:absolute;top:253px;width:152px;text-align:center;font-size:5px;color:#555}

  .brand{position:absolute;display:flex;align-items:center;gap:3px}
  .brand-mark{width:9px;height:9px;background:var(--grey)}
  .brand-name{font-family:"Roboto Condensed",Arial,sans-serif;font-weight:700;color:var(--red);font-size:5.6px;line-height:5.4px;text-transform:uppercase;letter-spacing:.2px}
  .brand-name.on-red{color:#fff}

  .fine{position:absolute;font-size:2.6px;line-height:3.6px;color:#555;white-space:nowrap}
  .fine.white{color:#fff}
  .fine.right{text-align:right}
  .fine.center{text-align:center;left:0;right:0}

  .swoosh{position:absolute;left:0;width:100%}
  .swoosh-bottom{bottom:0;height:42px}
  .swoosh-top{top:0;height:36px}

  .fax-title{position:absolute;left:9px;top:60px;font-size:10px;letter-spacing:.5px;color:#222}
  .fax-fields{position:absolute;left:9px;top:78px;width:134px;display:grid;grid-template-columns:1fr 1fr;column-gap:8px;row-gap:4px}
  .fax-field{font-size:2.8px;color:#555;border-bottom:.4px solid #999;padding-bottom:1px}
  .fax-checks{position:absolute;left:9px;top:145px;width:134px;display:flex;justify-content:space-between}
  .fax-check{display:flex;align-items:center;gap:2px;font-size:2.6px;color:#555}
  .fax-check i{width:4px;height:4px;border:.4px solid #777;display:block}

  .envelope{position:absolute;background:var(--paper);box-shadow:0 1px 3px rgba(0,0,0,.25);overflow:hidden}
  .envelope-back{left:771px;top:58px;width:144px;height:80px}
  .envelope-front{left:735px;top:96px;width:180px;height:114px}

  .slip{position:absolute;left:990px;top:58px;width:170px;height:72px;background:var(--paper);box-shadow:0 1px 3px rgba(0,0,0,.25);overflow:hidden}
  .slip-title{position:absolute;right:6px;top:4px;font-size:7.5px;color:var(--red)}

  .card{position:absolute;border-radius:4px;overflow:hidden;box-shadow:0 1px 3px rgba(0,0,0,.3)}
  .card-front{left:920px;top:145px;width:126px;height:65px;background:var(--paper)}
  .card-back{left:1057px;top:151px;width:103px;height:60px;background:linear-gradient(135deg,var(--red-light),var(--red) 45%,var(--red-deep))}
  .card-name{position:absolute;right:5px;top:24px;font-size:4.2px;font-weight:700;color:var(--ink);text-align:right;line-height:5px}
  .card-name span{display:block;font-weight:400;font-size:3px;color:#666}
  .card-url{position:absolute;right:8px;top:27px;font-size:4.4px;color:#fff}
</style>
</head>
<body>
<svg width="0" height="0" style="position:absolute" aria-hidden="true">
  <defs>
    <linearGradient id="redFill" x1="0" y1="0" x2="1" y2="1">
      <stop offset="0" stop-color="#7c0a11"/>
      <stop offset=".5" stop-color="#c3121c"/>
      <stop offset="1" stop-color="#8d0b13"/>
    </linearGradient>
    <symbol id="wave-bottom" viewBox="0 0 152 42" preserveAspectRatio="none">
      <path d="M0 30 C45 24 90 6 152 3 L152 42 L0 42 Z" fill="#9a9a9a"/>
      <path d="M0 33 C45 27 90 10 152 7 L152 42 L0 42 Z" fill="#fff"/>
      <path d="M0 35 C45 29 90 13 152 10 L152 42 L0 42 Z" fill="url(#redFill)"/>
    </symbol>
    <symbol id="wave-top" viewBox="0 0 152 36" preserveAspectRatio="none">
      <path d="M0 0 H152 V8 C100 10 55 30 0 27 Z" fill="#9a9a9a"/>
      <path d="M0 0 H152 V6 C100 8 55 27 0 24 Z" fill="#fff"/>
      <path d="M0 0 H152 V4 C100 6 55 25 0 22 Z" fill="url(#redFill)"/>
    </symbol>
  </defs>
</svg>

<main class="canvas">

  <!-- Letterhead: option 1 -->
  <section class="sheet letter" style="left:37px">
    <div class="brand" style="left:42px;top:8px"><div class="brand-mark"></div><div class="brand-name">Brell<br>Haulage<br>Contracting</div></div>
    <p class="fine" style="left:8px;top:196px">P.O Box 817 Wattlegrove WA, 6958</p>
    <p class="fine" style="left:8px;top:201px">08 9352 7140 &nbsp; brellhaul@mailbox-example.com.au &nbsp; www.brellhaul-example.com.au</p>
    <p class="fine" style="left:8px;top:206px">Brell Holdings Pty Ltd (ACN 582 316 907) ATF The Brell Discretionary Trust T/AS &nbsp; ABN 71 834 209 553</p>
  </section>
  <p class="option-label" style="left:37px">Option 1</p>

  <!-- Letterhead: option 2 -->
  <section class="sheet letter" style="left:213px">
    <div class="brand" style="left:42px;top:8px"><div class="brand-mark"></div><div class="brand-name">Brell<br>Haulage<br>Contracting</div></div>
    <svg class="swoosh swoosh-bottom"><use href="#wave-bottom"/></svg>
    <p class="fine white right" style="right:6px;top:184px">08 9352 7140<br>brellhaul@mailbox-example.com.au<br>www.brellhaul-example.com.au<br>P.O Box 817 Wattlegrove WA, 6958</p>
    <p class="fine white center" style="top:200px">ABN 71 834 209 553<br>Brell Holdings Pty Ltd (ACN 582 316 907) ATF The Brell Discretionary Trust T/AS</p>
  </section>
  <p class="option-label" style="left:213px">Option 2</p>

  <!-- Letterhead: option 3 -->
  <section class="sheet letter" style="left:390px">
    <svg class="swoosh swoosh-top"><use href="#wave-top"/></svg>
    <p class="fine white" style="left:6px;top:3px">P.O Box 817 Wattlegrove WA, 6958<br>08 9352 7140<br>brellhaul@mailbox-example.com.au<br>www.brellhaul-example.com.au</p>
    <div class="brand" style="right:8px;top:22px"><div class="brand-mark"></div><div class="brand-name">Brell<br>Haulage<br>Contracting</div></div>
    <p class="fine center" style="top:204px">ABN 71 834 209 553<br>Brell Holdings Pty Ltd (ACN 582 316 907) ATF The Brell Discretionary Trust T/AS</p>
  </section>
  <p class="option-label" style="left:390px">Option 3</p>

  <!-- Fax cover: option 4 -->
  <section class="sheet letter" style="left:570px">
    <div class="brand" style="left:42px;top:8px"><div class="brand-mark"></div><div class="brand-name">Brell<br>Haulage<br>Contracting</div></div>
    <p class="fine center" style="top:27px">Brell Holdings Pty Ltd (ACN 582 316 907) ATF The Brell Discretionary Trust T/AS</p>
    <h1 class="fax-title">FAX</h1>
    <div class="fax-fields">
      <span class="fax-field">To:</span><span class="fax-field">From:</span>
      <span class="fax-field">Fax:</span><span class="fax-field">Pages:</span>
      <span class="fax-field">Phone:</span><span class="fax-field">Date:</span>
      <span class="fax-field">Re:</span><span class="fax-field">cc:</span>
    </div>
    <div class="fax-checks">
      <span class="fax-check"><i></i>Urgent</span>
      <span class="fax-check"><i></i>For Review</span>
      <span class="fax-check"><i></i>Please Comment</span>
      <span class="fax-check"><i></i>Please Reply</span>
      <span class="fax-check"><i></i>Please Recycle</span>
    </div>
    <svg class="swoosh swoosh-bottom"><use href="#wave-bottom"/></svg>
    <p class="fine white right" style="right:6px;top:184px">08 9352 7140<br>brellhaul@mailbox-example.com.au<br>www.brellhaul-example.com.au<br>P.O Box 817 Wattlegrove WA, 6958</p>
    <p class="fine white center" style="top:204px">ABN 71 834 209 553</p>
  </section>
  <p class="option-label" style="left:570px">Option 4</p>

  <!-- Envelope: back with flap -->
  <section class="envelope envelope-back">
    <svg width="144" height="80" viewBox="0 0 144 80" style="position:absolute;inset:0">
      <path d="M0 0 H144 V12 L72 40 L0 12 Z" fill="url(#redFill)"/>
      <path d="M0 12 L72 40 L144 12" fill="none" stroke="#ddd" stroke-width=".6"/>
    </svg>
    <div class="brand" style="left:52px;top:5px"><div class="brand-name on-red">Brell<br>Haulage</div></div>
  </section>

  <!-- Envelope: front -->
  <section class="envelope envelope-front">
    <svg width="180" height="114" viewBox="0 0 180 114" style="position:absolute;inset:0">
      <path d="M0 0 L90 38 L180 0" fill="none" stroke="#d6d6d6" stroke-width=".6"/>
    </svg>
    <div class="brand" style="left:6px;top:40px"><div class="brand-mark"></div><div class="brand-name">Brell<br>Haulage<br>Contracting</div></div>
    <svg class="swoosh" style="bottom:0;height:44px" viewBox="0 0 152 42" preserveAspectRatio="none"><use href="#wave-bottom"/></svg>
    <p class="fine white right" style="right:6px;top:96px">www.brellhaul-example.com.au<br>P.O Box 817 Wattlegrove WA, 6958</p>
  </section>

  <!-- With compliments slip -->
  <section class="slip">
    <div class="brand" style="left:6px;top:6px"><div class="brand-mark"></div><div class="brand-name">Brell<br>Haulage<br>Contracting</div></div>
    <p class="slip-title">With Compliments</p>
    <p class="fine" style="left:6px;top:28px">08 9352 7140<br>brellhaul@mailbox-example.com.au<br>www.brellhaul-example.com.au<br>P.O Box 817 Wattlegrove WA, 6958</p>
    <svg class="swoosh" style="bottom:0;height:34px" viewBox="0 0 152 42" preserveAspectRatio="none"><use href="#wave-bottom"/></svg>
  </section>

  <!-- Business card: front -->
  <section class="card card-front">
    <div class="brand" style="left:5px;top:6px"><div class="brand-mark"></div><div class="brand-name">Brell<br>Haulage<br>Contracting</div></div>
    <p class="card-name">Your Name<span>Title</span></p>
    <svg class="swoosh" style="bottom:0;height:34px" viewBox="0 0 152 42" preserveAspectRatio="none"><use href="#wave-bottom"/></svg>
    <p class="fine white right" style="right:5px;top:38px">08 9352 7140<br>brellhaul@mailbox-example.com.au<br>www.brellhaul-example.com.au<br>P.O Box 817 Wattlegrove WA, 6958</p>
  </section>

  <!-- Business card: back -->
  <section class="card card-back">
    <p class="card-url">www.brellhaul-example.com</p>
  </section>

</main>
</body>
</html>
```